Web Design Project

Please take a look at my current aged website www.talvikhrconsulting.com and my newly designed logo and business cards. I would like a new fresh updated look to my website and my new designs incorporated.
Updates

  Good Morning Everyone

Due to an Austrralian licencing issue I have had to have my logo slightly redesigned.

Would you please be able to look at the newly uploaded files and revise your designs.

Thanks so much.  I am very happy with the calibre and quality of the designs so far.

kind Regards

Marla

Industry/Entity Type

Business

Requirements
Must have
• the exisiting pages and fresh new graphics and a real commitment to my palette of lime green, turqouise and black.

```html
<!DOCTYPE html>
<html lang="en">
<head>
<meta charset="utf-8">
<title>Talvik Consulting</title>
<link rel="stylesheet" href="https://fonts.googleapis.com/css2?family=Arimo:wght@400;700&display=swap">
<style>
:root{
  --backdrop:#2a9bab;
  --ink:#050708;
  --pale:#eef7ee;
  --heading:#0c5e6b;
  --teal:#1fa6b8;
  --teal-deep:#137d8c;
  --lime:#8cc63f;
  --lime-deep:#6fa82a;
  --text:#3a3a3a;
}
*{margin:0;padding:0;box-sizing:border-box}
html,body{width:1200px;height:666px;overflow:hidden}
body{background:var(--backdrop);font-family:"Arimo",Arial,sans-serif;position:relative}
.page{position:absolute;left:175px;top:0;width:848px;height:589px;background:var(--pale);border-left:4px solid #fff;border-right:4px solid #fff}
.masthead{position:absolute;left:0;top:0;width:100%;height:244px;background:var(--ink)}
.brand{position:absolute;left:28px;top:20px;display:flex;align-items:center;gap:8px}
.brand-mark{width:52px;height:52px;border-radius:50%;border:4px solid var(--teal)}
.brand-name{font-size:23px;font-weight:700;color:var(--lime);letter-spacing:-.3px}
.tabs{position:absolute;left:477px;top:64px;display:flex;gap:2px;list-style:none}
.tabs li{width:87px;height:23px;background:linear-gradient(#fff,#e3eedb);border-top:3px solid var(--lime);border-radius:5px 5px 0 0;text-align:center;font-size:12.5px;line-height:21px;color:var(--ink)}
.main-nav{position:absolute;left:44px;top:107px;list-style:none}
.main-nav li{color:#fff;font-size:11px;height:19px;display:flex;align-items:center;gap:8px}
.main-nav svg{width:10px;height:8px}
.hero{position:absolute;left:206px;top:87px;width:621px;height:240px;box-shadow:0 4px 5px rgba(0,0,0,.45);display:flex}
.hero-art{width:319px;height:100%;background:linear-gradient(180deg,#c9d6db 0%,#93a9b0 40%,#26322f 70%,#eef3f2 100%)}
.hero-copy{flex:1;background:linear-gradient(var(--teal),var(--teal-deep));padding:27px 40px 0 13px;color:#fff;border-left:4px solid var(--lime)}
.hero-copy p{font-size:16.5px;font-weight:700;line-height:20px}
.hero-copy .hero-tag{font-size:20px;margin-top:24px}
.browse{display:block;margin-top:22px;width:43px;height:33px;background:linear-gradient(var(--lime),var(--lime-deep));border-radius:2px;font-size:7.5px;font-weight:700;color:#fff;text-align:center;padding-top:8px;line-height:8px}
h2{position:absolute;top:348px;font-size:16px;font-weight:700;color:var(--heading)}
.intro{position:absolute;left:27px;width:358px;font-size:10.5px;line-height:15.5px;color:var(--text)}
.read-more{position:absolute;left:306px;top:512px;font-size:10.5px;color:var(--heading);display:flex;gap:6px;align-items:center}
.jobs{position:absolute;left:378px;top:375px;width:280px;height:144px;border:1px solid #c9dcc1;border-top:3px solid var(--lime);background:var(--pale)}
.job{position:absolute;height:30px;background:#fff;font-size:12px;font-weight:700;color:var(--heading);display:flex;align-items:center;justify-content:center}
.news{position:absolute;left:672px;top:383px;list-style:none}
.news li{font-size:10.5px;color:#111;height:20px;display:flex;align-items:center;gap:6px}
.dot{width:13px;height:13px;border-radius:50%;background:var(--lime)}
.footer{position:absolute;left:0;bottom:0;width:100%;height:42px;background:var(--ink);color:#ccc;font-size:9.5px;border-top:3px solid var(--lime)}
.footer-nav{position:absolute;left:17px;top:14px;white-space:pre}
.copyright{position:absolute;right:13px;top:12px;font-size:11.5px}
</style>
</head>
<body>
<div class="page">
  <header class="masthead">
    <div class="brand"><span class="brand-mark"></span><span class="brand-name">Talvik Consulting</span></div>
    <ul class="tabs"><li>Downloads</li><li>Portfolio</li><li>Clients</li><li>Sitemap</li></ul>
    <ul class="main-nav">
      <li><svg viewBox="0 0 10 8"><path d="M0 4h8M5 1l3 3-3 3" stroke="#8cc63f" fill="none"/></svg>HOME</li>
      <li><svg viewBox="0 0 10 8"><path d="M0 4h8M5 1l3 3-3 3" stroke="#8cc63f" fill="none"/></svg>OUR SERVICES</li>
      <li><svg viewBox="0 0 10 8"><path d="M0 4h8M5 1l3 3-3 3" stroke="#8cc63f" fill="none"/></svg>OUR CONSULTANTS</li>
      <li><svg viewBox="0 0 10 8"><path d="M0 4h8M5 1l3 3-3 3" stroke="#8cc63f" fill="none"/></svg>OUR FEES</li>
      <li><svg viewBox="0 0 10 8"><path d="M0 4h8M5 1l3 3-3 3" stroke="#8cc63f" fill="none"/></svg>CAREER</li>
      <li><svg viewBox="0 0 10 8"><path d="M0 4h8M5 1l3 3-3 3" stroke="#8cc63f" fill="none"/></svg>CONTACT US</li>
    </ul>
  </header>
  <section class="hero">
    <div class="hero-art" role="img" aria-label="Silhouettes of business people standing before a world map"></div>
    <div class="hero-copy">
      <p>Take a look at Our Services to see how our comprehensive consultancy can add value to your business.</p>
      <p class="hero-tag">Lorem ipsum dolor. !!</p>
      <span class="browse">BROWSE<br>NOW</span>
    </div>
  </section>
  <h2 style="left:27px">What can Talvik HR Consulting do for me?</h2>
  <p class="intro" style="top:384px">During these challenging economic times it can be difficult to justify internal human resources management services or support. However as a business owner or Manager you may find that HR support or advice is required from time to time.</p>
  <p class="intro" style="top:460px">Talvik HR Consulting are an outsourced HR function.&nbsp; We can provide you with that ongoing support, offer solutions and assist you with developing strategies that fit your business and deliver results.</p>
  <span class="read-more"><svg width="10" height="8" viewBox="0 0 10 8"><path d="M0 4h8M5 1l3 3-3 3" stroke="#6fa82a" fill="none"/></svg>read more</span>
  <h2 style="left:381px">Newly posted jobs</h2>
  <div class="jobs">
    <div class="job" style="left:23px;top:8px;width:75px">Norvale</div>
    <div class="job" style="left:152px;top:10px;width:110px">Brightwell</div>
    <div class="job" style="left:10px;top:56px;width:110px">Brightwell</div>
    <div class="job" style="left:127px;top:60px;width:96px">Kestrel Tech</div>
    <div class="job" style="left:230px;top:60px;width:44px">Ondo</div>
    <div class="job" style="left:10px;top:106px;width:105px">Harbor Finance</div>
    <div class="job" style="left:158px;top:108px;width:105px">Harbor Finance</div>
  </div>
  <h2 style="left:679px;top:350px">News and events</h2>
  <ul class="news">
    <li><span class="dot"></span>Lorem ipsum dolor sit amet.</li>
    <li><span class="dot"></span>Cum sociis natoque penatibus.</li>
    <li><span class="dot"></span>Aenean commodo ligula.</li>
    <li><span class="dot"></span>Cum sociis natoque penatibus.</li>
    <li><span class="dot"></span>Aenean commodo&nbsp; dolor.</li>
    <li><span class="dot"></span>Deneo&nbsp; ligula eget dolor.</li>
  </ul>
  <footer class="footer">
    <div class="footer-nav">HOME   |  ABOUT US  |  PRODUCTS     |     SERVICES     |     CONTACT US</div>
    <div class="copyright">Copyright © 2012 Talvik Consulting Pty Ltd</div>
  </footer>
</div>
</body>
</html>
```